Business Card Design Project

Basic business card with minimal details. I just need company name, email & web address, telephone and my name.
I would like the back of the card to be grey with my logo & company name centred.

Target Market(s)

Architects
Builders
Property Developers

Industry/Entity Type

Business

Font styles to use
Sans Serif

Colors

Designer to choose colors to be used in the design.

Requirements
Must have
• Tallow Crest
Rupert Hazelby - Director
M: 0427 915203
E: rupert@tallowcrest.com.au
W: www.tallowcrest.com.au
Should not have
• No other images or pictures

```html
<!DOCTYPE html>
<html lang="en">
<head>
<meta charset="utf-8">
<title>Tallow Crest – Business Card</title>
<link rel="stylesheet" href="https://fonts.googleapis.com/css2?family=Titillium+Web:wght@400;600&display=swap">
<style>
  :root {
    --page-bg: #e6e6e8;
    --card-white: #ffffff;
    --divider: #7d93a8;
    --brand-steel: #4b6074;
    --crimson-light: #e9365f;
    --crimson-mid: #d42a4e;
    --crimson-deep: #a51b35;
    --ink-light: #ffffff;
  }
  * { margin: 0; padding: 0; box-sizing: border-box; }
  html, body {
    width: 1200px; height: 900px; overflow: hidden;
    background: var(--page-bg);
    font-family: "Titillium Web", sans-serif;
  }
  .card {
    position: absolute; left: 65px; top: 152px;
    width: 1070px; height: 614px;
    display: flex;
  }
  .card-brand {
    width: 510px; height: 100%;
    background: var(--card-white);
    border-right: 4px solid var(--divider);
    display: flex; align-items: center; justify-content: center;
  }
  .brand-name {
    color: var(--brand-steel);
    font-weight: 600;
    font-size: 44px;
    letter-spacing: 3px;
    text-transform: uppercase;
  }
  .card-contact {
    position: relative; flex: 1; height: 100%;
    background:
      linear-gradient(100deg, rgba(255,255,255,0.12) 0%, rgba(255,255,255,0.05) 35%, rgba(255,255,255,0) 50%),
      linear-gradient(90deg, var(--crimson-light) 0%, var(--crimson-mid) 45%, var(--crimson-deep) 100%);
    color: var(--ink-light);
  }
  .person { position: absolute; left: 98px; top: 130px; }
  .person-name { font-size: 35px; font-weight: 600; line-height: 1; letter-spacing: 0.5px; text-transform: uppercase; }
  .person-role { font-size: 21px; line-height: 1.3; }
  .contact-list { position: absolute; left: 40px; top: 256px; list-style: none; }
  .contact-item { display: flex; align-items: flex-start; font-size: 25px; line-height: 31px; margin-bottom: 16px; }
  .contact-icon { width: 32px; height: 31px; margin-right: 26px; flex: none; fill: var(--ink-light); }
</style>
</head>
<body>
<div class="card">
  <section class="card-brand">
    <h1 class="brand-name">Tallow Crest</h1>
  </section>
  <section class="card-contact">
    <div class="person">
      <h2 class="person-name">Rupert Hazelby</h2>
      <p class="person-role">Director</p>
    </div>
    <ul class="contact-list">
      <li class="contact-item">
        <svg class="contact-icon" viewBox="0 0 32 31"><path d="M3 9c0-3 5-5 13-5s13 2 13 5v2h-6V9c-2-1-4-1-7-1s-5 0-7 1v2H3z"/><path d="M8 12h16l3 13H5z"/></svg>
        0427 915203
      </li>
      <li class="contact-item">
        <svg class="contact-icon" viewBox="0 0 32 31"><rect x="2" y="5" width="28" height="21" fill="none" stroke="#fff" stroke-width="2"/><path d="M2 5l14 12L30 5M2 26l10-10M30 26L20 16" fill="none" stroke="#fff" stroke-width="1.6"/></svg>
        rupert@tallowcrest.com.au
      </li>
      <li class="contact-item">
        <svg class="contact-icon" viewBox="0 0 32 31"><rect x="3" y="4" width="26" height="18" fill="none" stroke="#fff" stroke-width="3"/><rect x="13" y="22" width="6" height="4"/><rect x="9" y="26" width="14" height="2"/></svg>
        www.tallowcrest.com.au
      </li>
      <li class="contact-item">
        <svg class="contact-icon" viewBox="0 0 32 31"><path d="M16 3L1 16l2 2 13-11 13 11 2-2z"/><path d="M6 17l10-8 10 8v12h-7v-8h-6v8H6z"/></svg>
        <span>Suite 00 Harbour Lane<br>Brookvale, NSW xxxx</span>
      </li>
    </ul>
  </section>
</div>
</body>
</html>
```